Stationery Design Project for Nimbora, Chicago

Nimbora, a street parking application which helps car drivers find a street parking spot by offering an ideal path along which to look for parking. This path is calculated by our algorithm based on data (e.g. historical data, baseball games schedule, etc.). Along this path the driver will find a spot and will also save 70% of the search time. Customer we target is reg. between 21 and 45 yo.

We envision something young, fresh, bright and original. Slightly abstract maybe. It should represent the idea and elements of finding street parking in the city, e.g. car(s), parking spot, people, city, etc. (just ideas!).

Logo is attached.

Requirement:
- Business Cards (2 Sided Full Color CMYK)
- Letterhead (1 Sided Full Color CMYK)
- Envelope (1 Sided Full Color CMYK)
- Sticker (1 Sided Full Color CMYK), round with a 2inch diameter.

Reason: We're starting to get more and more designs and need more time to look into all of them. Very exciting!! Thanks to everybody!

Hi all, we're in the process of selecting our favs. Though choices!!! Really good submissions. Will keep you posted and sorry for the delay.

Target Market(s)

Car drivers and owners between 21 and 45

Industry/Entity Type

Parking

Requirements
Must have
• Sticker should be round and include company URL nimbora.com and the new logo which we will attach soon.
Should not have
• Should not be too serious or boring.

```html
<!DOCTYPE html>
<html lang="en">
<head>
<meta charset="utf-8">
<title>Nimbora Business Cards</title>
<link rel="stylesheet" href="https://fonts.googleapis.com/css2?family=Source+Sans+3:wght@400;600;700&display=swap">
<style>
  :root {
    --stage: #a8812a;
    --card-white: #ffffff;
    --brand-blue: #2a5fc4;
    --brand-blue-deep: #1f3a9a;
    --brand-blue-light: #3fc4f5;
    --ink: #1c1c1c;
    --ring-dark: #202020;
    --back-dark: #2b2b2b;
    --back-black: #000000;
    --text-light: #ffffff;
  }
  * { margin: 0; padding: 0; box-sizing: border-box; }
  html, body { width: 1200px; height: 686px; overflow: hidden; }
  body {
    background: var(--stage);
    font-family: "Source Sans 3", sans-serif;
    position: relative;
  }
  .card {
    position: absolute;
    width: 448px;
    height: 257px;
    overflow: hidden;
    box-shadow: 1px 2px 3px rgba(0,0,0,0.35);
  }
  .card-front { left: 120px; top: 67px; background: var(--card-white); }
  .card-logo-side { left: 629px; top: 67px; background: var(--card-white); }
  .card-back {
    left: 375px; top: 372px;
    background: radial-gradient(circle at 18% 18%, #5a5a5a 0%, var(--back-dark) 30%, #141414 65%, var(--back-black) 100%);
  }
  .card-arc { position: absolute; inset: 0; }

  .brand {
    position: absolute;
    display: flex;
    align-items: center;
    font-weight: 600;
    color: var(--ink);
  }
  .brand-dot {
    border-radius: 50%;
    background: radial-gradient(circle at 45% 40%, var(--brand-blue-light), var(--brand-blue) 55%, var(--brand-blue-deep));
    flex: none;
  }
  .card-front .brand { left: 18px; top: 106px; font-size: 30px; gap: 10px; }
  .card-front .brand-dot { width: 52px; height: 52px; }
  .card-logo-side .brand { left: 57px; top: 85px; font-size: 58px; gap: 18px; }
  .card-logo-side .brand-dot { width: 100px; height: 100px; }
  .card-back .brand { left: 0; right: 0; top: 0; bottom: 0; justify-content: center; flex-direction: column; gap: 0; }
  .card-back .brand-dot { width: 138px; height: 138px; box-shadow: 0 0 0 10px rgba(255,255,255,0.06); }

  .contact {
    position: absolute;
    right: 25px;
    top: 48px;
    text-align: right;
    color: var(--text-light);
    font-size: 13.5px;
    line-height: 1.25;
  }
  .contact-name { font-size: 17.5px; font-weight: 700; }
  .contact-title { font-size: 13.5px; font-weight: 700; margin-bottom: 14px; }
  .contact-address { margin-bottom: 14px; }
  .contact-line { display: flex; justify-content: flex-end; align-items: center; gap: 6px; height: 19px; }
  .contact-line svg { width: 11px; height: 11px; fill: var(--text-light); flex: none; }
</style>
</head>
<body>

<section class="card card-front" aria-label="Business card front">
  <svg class="card-arc" viewBox="0 0 448 257" aria-hidden="true">
    <defs>
      <radialGradient id="blueSweep" cx="0.18" cy="0.32" r="0.75">
        <stop offset="0" stop-color="#44c8f7"/>
        <stop offset="0.45" stop-color="#2f76d2"/>
        <stop offset="1" stop-color="#23319a"/>
      </radialGradient>
    </defs>
    <circle cx="553" cy="150" r="333" fill="var(--ring-dark)"/>
    <circle cx="560" cy="136" r="327" fill="var(--card-white)"/>
    <circle cx="560" cy="128" r="320" fill="url(#blueSweep)"/>
  </svg>

  <div class="brand"><span class="brand-dot"></span><span class="brand-name">Nimbora</span></div>

  <div class="contact">
    <div class="contact-name">Your Name</div>
    <div class="contact-title">Title</div>
    <div class="contact-address">Street name<br>City, State, zip code</div>
    <div class="contact-line">123-456-7890
      <svg viewBox="0 0 12 12"><path d="M2.5 1l2 2.3-1 1.2c.7 1.5 1.8 2.6 3.1 3.2l1.1-1 2.3 2-1.2 1.6C5.3 10 2 6.7 1.1 3z"/></svg>
    </div>
    <div class="contact-line">123-456-7890
      <svg viewBox="0 0 12 12"><path d="M3 1h5l1 1v2H3zM1 5h10v4H9v2H3V9H1zm3 3v2h4V8z"/></svg>
    </div>
    <div class="contact-line">name@website.com
      <svg viewBox="0 0 12 12"><path d="M1 3h10v6H1zm1 .6L6 6.3l4-2.7z" fill-rule="evenodd"/></svg>
    </div>
    <div class="contact-line">www.website.com
      <svg viewBox="0 0 12 12"><path d="M6 1a5 5 0 100 10A5 5 0 006 1zm0 1c.6.7 1 1.7 1.1 3H4.9C5 3.7 5.4 2.7 6 2zM2.1 5.5h1.8c0 1 .2 2 .6 2.8A4 4 0 012.1 5.5zm0-1A4 4 0 014.5 2c-.4.8-.6 1.7-.6 2.5zm2.8 1h2.2c0 1.3-.5 2.4-1.1 3.2-.6-.8-1.1-1.9-1.1-3.2zm3.2 0h1.8a4 4 0 01-2.4 2.8c.4-.8.6-1.8.6-2.8zm0-1c0-.8-.2-1.7-.6-2.5a4 4 0 012.4 2.5z"/></svg>
    </div>
  </div>
</section>

<section class="card card-logo-side" aria-label="Business card logo side">
  <div class="brand"><span class="brand-dot"></span><span class="brand-name">Nimbora</span></div>
</section>

<section class="card card-back" aria-label="Business card back">
  <div class="brand" aria-label="Nimbora"><span class="brand-dot"></span></div>
</section>

</body>
</html>
```